holloway paving service

Needs to have phone number 0418259730 and email markholloway@brightmail.com.au.
ABN 62318470915
name mark holloway

For all your concreting solutions
Excavation
Exposed & colour concrete
House & shed slabs
Driveways
Landing & steps

Contact Information for Business Card

ph 0418259730
email markholloway@brightmail.com.au.
ABN 62318470915
name mark holloway

```html
<!DOCTYPE html>
<html lang="en">
<head>
<meta charset="utf-8">
<title>Holloway Paving Service – Business Card</title>
<link href="https://fonts.googleapis.com/css2?family=Montserrat:wght@400;500;600;700&family=Roboto:wght@400&display=swap" rel="stylesheet">
<style>
  :root {
    --orange: #f26a21;
    --grey: #666666;
    --text-dark: #4a4a4a;
    --card-white: #f3f3f3;
    --backdrop: #2b2b2b;
    --white: #ffffff;
  }
  * { margin: 0; padding: 0; box-sizing: border-box; }
  html, body { width: 1200px; height: 960px; overflow: hidden; }
  body { background: var(--backdrop); position: relative; font-family: "Montserrat", sans-serif; }

  .card { position: absolute; width: 600px; height: 342px; }
  .card--front { left: 322px; top: 110px; background: var(--card-white); }
  .card--back { left: 320px; top: 493px; background: var(--orange); }

  .brand { position: absolute; left: 26px; top: 28px; width: 240px; text-align: center; }
  .brand__name { color: var(--orange); font-weight: 700; font-size: 19px; letter-spacing: 0.2px; line-height: 1.1; }
  .brand__sub { display: flex; align-items: center; gap: 10px; color: var(--grey); font-weight: 500; font-size: 15px; letter-spacing: 2px; line-height: 1.1; }
  .brand__sub::before, .brand__sub::after { content: ""; flex: 1; height: 2px; background: var(--grey); }
  .brand__phone { color: var(--orange); font-weight: 500; font-size: 15px; letter-spacing: 1.5px; line-height: 1.1; }

  .person { position: absolute; left: 26px; top: 156px; }
  .person__name { color: var(--orange); font-weight: 600; font-size: 22px; letter-spacing: 0.3px; }
  .person__abn { color: var(--grey); font-size: 14px; margin-top: 6px; letter-spacing: 0.3px; }
  .contact { list-style: none; margin-top: 4px; }
  .contact li { display: flex; align-items: center; gap: 7px; color: var(--grey); font-size: 14px; height: 19.5px; }
  .contact svg { width: 12px; height: 12px; flex: none; fill: var(--orange); }
  .services { margin-top: 6px; font-family: "Roboto", sans-serif; color: var(--text-dark); font-size: 14px; line-height: 18px; }

  .front-mark { position: absolute; left: 380px; top: 112px; display: flex; align-items: center; gap: 12px; }
  .front-mark__square { width: 56px; height: 56px; background: var(--grey); }
  .front-mark__name { color: var(--orange); font-weight: 700; font-size: 17px; line-height: 1.15; }

  .back-lockup { position: absolute; left: 118px; top: 118px; display: flex; align-items: center; }
  .back-lockup__square { width: 62px; height: 62px; background: var(--white); }
  .back-lockup__rule { width: 2px; height: 102px; background: var(--white); margin: 0 8px 0 46px; }
  .back-lockup .brand { position: static; width: 244px; }
  .back-lockup .brand__name, .back-lockup .brand__sub, .back-lockup .brand__phone { color: var(--white); }
  .back-lockup .brand__sub::before, .back-lockup .brand__sub::after { background: var(--white); }
</style>
</head>
<body>
  <section class="card card--front">
    <div class="brand">
      <div class="brand__name">HOLLOWAY PAVING</div>
      <div class="brand__sub">SERVICE</div>
      <div class="brand__phone">0418259730</div>
    </div>

    <div class="person">
      <div class="person__name">MARK HOLLOWAY</div>
      <div class="person__abn">ABN 62318470915</div>
      <ul class="contact">
        <li><svg viewBox="0 0 24 24"><path d="M6.6 10.8a15.1 15.1 0 0 0 6.6 6.6l2.2-2.2c.3-.3.7-.4 1-.2 1.1.4 2.3.6 3.6.6.6 0 1 .4 1 1V20c0 .6-.4 1-1 1A17 17 0 0 1 3 4c0-.6.4-1 1-1h3.5c.6 0 1 .4 1 1 0 1.3.2 2.5.6 3.6.1.3 0 .7-.2 1z"/></svg>0418259730</li>
        <li><svg viewBox="0 0 24 24"><path d="M2 5h20v14H2z M2 5l10 7 10-7" /></svg>markholloway@brightmail.com.au</li>
        <li><svg viewBox="0 0 24 24"><circle cx="12" cy="12" r="10"/></svg>www.hollowaypaving.com.au</li>
      </ul>
      <div class="services">
        Excavation | Exposed &amp; colour concrete<br>
        House &amp; shed slabs | Driveways | Landing &amp; steps
      </div>
    </div>

    <div class="front-mark">
      <div class="front-mark__square"></div>
      <div class="front-mark__name">HOLLOWAY<br>PAVING<br>SERVICE</div>
    </div>
  </section>

  <section class="card card--back">
    <div class="back-lockup">
      <div class="back-lockup__square"></div>
      <div class="back-lockup__rule"></div>
      <div class="brand">
        <div class="brand__name">HOLLOWAY PAVING</div>
        <div class="brand__sub">SERVICE</div>
        <div class="brand__phone">0418259730</div>
      </div>
    </div>
  </section>
</body>
</html>
```